Design and Renovation Company Luxury Business Card

I want to create a luxury business card for a Design and Renovation Firm . We will use our current logo. The company name is 528BUILDA. We do not want anything standard. We need a very unique concept.
Please see uploaded inspiration. I really like the textured paper option. I would like the card to be thick with debossing, and/or embossing options. The logo has orange in it but I would like to see the card with and without the orange. I think the orange may make the company feel less high-end. The goal is to elevate the logo not match its vibe per se of the logo. We want something very unique, not standard at all!
I would like a space for :
Logo,
Name,
Position,
Email,
Office number,
Website Address,
Business Address,
Thank you!
Have fun!
Target Market(s)
Home owners Age 35 +
Industry/Entity Type
Design and Renovation
Contact Information for Business Card
Logo, Name, Position, Email, Office number, Website Address, Business Address,.
Colors
Designer to choose colors to be used in the design.
Requirements
Must have
- A luxury designer feel. Must be black or dark grey but open to other luxury ideas.
Nice to have
- Gold, silver, black embossing or debossing. Textured paper design.
Should not have
- A cheap look and feel.

```html
<!DOCTYPE html>
<html lang="en">
<head>
<meta charset="utf-8">
<title>528BUILDA — Business Card</title>
<link rel="stylesheet" href="https://fonts.googleapis.com/css2?family=Arimo:wght@400;700&display=swap">
<style>
  :root {
    --page-bg: #b9b9b9;
    --card-black: #000000;
    --ink-white: #ffffff;
    --gold: #e6c46a;
    --gold-soft: #d9c48e;
    --cream: #efe6cf;
    --divider: #6b5a2e;
  }
  * { margin: 0; padding: 0; box-sizing: border-box; }
  html, body {
    width: 1135px; height: 1200px; overflow: hidden;
    background: var(--page-bg);
  }
  .canvas {
    position: relative; width: 1135px; height: 1200px;
    display: flex; flex-direction: column; align-items: center;
    gap: 40px; padding-top: 32px;
  }
  .card {
    position: relative; width: 960px; height: 548px;
    background: var(--card-black);
    box-shadow: 0 4px 14px rgba(0,0,0,.25);
  }

  /* Front */
  .front-brand {
    position: absolute; left: 0; right: 0; top: 214px;
    text-align: center; color: var(--ink-white);
    font-family: "Arimo", sans-serif; font-weight: 400;
  }
  .front-brand .company-name {
    font-size: 80px; line-height: 1; letter-spacing: 2px;
  }
  .front-brand .tagline {
    margin-top: 8px; font-size: 22px; letter-spacing: 3px;
  }

  /* Back */
  .back-brand {
    position: absolute; left: 0; right: 0; top: 50px;
    text-align: center; color: var(--ink-white);
    font-family: "Arimo", sans-serif; font-weight: 400;
  }
  .back-brand .company-name {
    font-size: 48px; line-height: 1; letter-spacing: 2px;
  }
  .back-brand .tagline {
    margin-top: 6px; font-size: 14px; letter-spacing: 2px;
  }

  .person {
    position: absolute; left: 80px; width: 270px; top: 350px;
    text-align: center; font-family: "Arimo", sans-serif;
  }
  .person .company {
    font-weight: 700; font-size: 34px; line-height: 1;
    letter-spacing: 4px; color: var(--gold);
  }
  .person .company-line {
    margin-top: 8px; font-size: 14px; color: var(--gold-soft);
  }
  .person .role {
    margin-top: 6px; font-size: 20px; color: var(--gold-soft);
  }

  .divider {
    position: absolute; left: 371px; top: 350px;
    width: 1px; height: 166px; background: var(--divider);
  }

  .contact {
    position: absolute; left: 406px; top: 358px;
    list-style: none;
    font-family: "Arimo", sans-serif; font-size: 21px; line-height: 34px;
  }
  .contact .phone, .contact .address { color: var(--cream); }
  .contact .web, .contact .email { color: var(--gold); }
</style>
</head>
<body>
  <main class="canvas">
    <section class="card card-front" aria-label="Business card front">
      <div class="front-brand">
        <div class="company-name">528BUILDA</div>
        <div class="tagline">Design and Renovation Firm</div>
      </div>
    </section>

    <section class="card card-back" aria-label="Business card back">
      <div class="back-brand">
        <div class="company-name">528BUILDA</div>
        <div class="tagline">Design and Renovation Firm</div>
      </div>

      <div class="person">
        <div class="company">528BUILDA</div>
        <div class="company-line">DESIGN AND RENOVATION FIRM</div>
        <div class="role">Ceo</div>
      </div>

      <div class="divider"></div>

      <ul class="contact">
        <li class="phone">+ 1 555 014 2271</li>
        <li class="address">Harbor City, Northland</li>
        <li class="web">www.528buildadesign.com</li>
        <li class="email">info@528buildadesign.com</li>
      </ul>
    </section>
  </main>
</body>
</html>
```